To design a brand identity that is simple and creative with 'Corvane' as the brand name, I like modern simple fonts like helvetica neue, I want to print both sides of the card, I am open to dark front and white back, but the design needs to transfer well to letter heads and email signatures, I am looking for sophisticated and elegant, but open minded about clever and off the wall, I do not do 'boring' Corvane Ventures is the mother company for a small group, specialising in Management & consulting, Software development and construction, we have a high level of integrity, we are transparent and accountable for what we do. my images are provided as a guide only, Im not expecting them to be just copied, Im looking for a creator and passionate thinker, who will put life into their work.

Target Market(s)

usually business minded people who are looking for something different in me, such as leadership, confidence and focus with thinking that is per haps a little outside the box..

Industry/Entity Type

Construction

Requirements
Must have
• clean, minmalistic
Nice to have
• custom logo
Should not have
• boring, traditional

```html
<!DOCTYPE html>
<html lang="en">
<head>
<meta charset="utf-8">
<title>Corvane Business Card</title>
<link rel="stylesheet" href="https://fonts.googleapis.com/css2?family=Quicksand:wght@300;400;700&display=swap">
<style>
  :root {
    --page: #e4e4e4;
    --card-top: #5c5c5c;
    --card-bottom: #424242;
    --brand: #d4622f;
    --text-light: #d6d6d6;
    --text-soft: #b4b4b4;
    --rose: #de4a63;
    --mauve: #8b4c7c;
    --teal: #2a9d88;
    --gold: #ebb63a;
    --berry: #b03a66;
    --plum: #8e3a6e;
    --violet: #7b44a0;
  }
  * { margin: 0; padding: 0; box-sizing: border-box; }
  html, body { width: 1200px; height: 900px; overflow: hidden; }
  body {
    background: var(--page);
    font-family: "Quicksand", "Helvetica Neue", sans-serif;
    position: relative;
  }
  .card {
    position: absolute;
    left: 250px;
    width: 700px;
    height: 400px;
    background: linear-gradient(160deg, var(--card-top), var(--card-bottom));
    overflow: hidden;
    box-shadow: 0 6px 18px rgba(0,0,0,0.18);
  }
  .card--back { top: 30px; }
  .card--front { top: 470px; }

  .pattern {
    position: absolute;
    background: linear-gradient(90deg, var(--rose), var(--mauve) 30%, var(--teal) 55%, var(--gold) 80%, var(--plum));
    opacity: 0.9;
  }
  .pattern--cool {
    background: linear-gradient(90deg, var(--violet), var(--berry) 40%, var(--gold) 70%, var(--teal));
  }
  .pattern--warm {
    background: linear-gradient(90deg, var(--gold), var(--berry) 55%, var(--plum));
  }

  .card--back .pattern--a { left: 20px; top: 0; width: 168px; height: 110px; }
  .card--back .pattern--b { left: 340px; top: 0; width: 162px; height: 150px; }
  .card--front .pattern--a { left: 20px; top: 0; width: 196px; height: 230px; }
  .card--front .pattern--b { left: 360px; top: 0; width: 190px; height: 215px; }
  .card--front .pattern--c { left: 620px; top: 110px; width: 80px; height: 150px; }

  .brand {
    position: absolute;
    display: flex;
    align-items: center;
    color: var(--brand);
    font-weight: 300;
    line-height: 1;
  }
  .brand__dot {
    border-radius: 50%;
    background: var(--brand);
  }
  .brand__tagline {
    position: absolute;
    font-weight: 300;
    color: var(--text-soft);
    letter-spacing: 0.04em;
  }

  .card--front .brand { left: 190px; top: 250px; font-size: 92px; gap: 22px; }
  .card--front .brand__dot { width: 46px; height: 46px; }
  .card--front .brand__tagline { left: 260px; top: 352px; font-size: 19px; }

  .card--back .brand { left: 515px; top: 170px; font-size: 38px; gap: 10px; }
  .card--back .brand__dot { width: 20px; height: 20px; }
  .card--back .brand__tagline { left: 547px; top: 214px; font-size: 11px; }

  .contact {
    position: absolute;
    left: 40px;
    top: 150px;
    color: var(--text-light);
    font-size: 17px;
    font-weight: 300;
    line-height: 1.35;
  }
  .contact__email { font-weight: 700; font-size: 19px; }
  .services {
    position: absolute;
    left: 40px;
    top: 300px;
    color: var(--text-light);
    font-size: 18px;
    font-weight: 300;
  }
  .phone {
    position: absolute;
    left: 420px;
    top: 258px;
    display: flex;
    align-items: center;
    gap: 8px;
    color: var(--text-light);
    font-size: 18px;
    font-weight: 400;
  }
</style>
</head>
<body>

<section class="card card--back">
  <div class="pattern pattern--a" role="img" aria-label="Decorative pattern of hanging colour bars"></div>
  <div class="pattern pattern--cool pattern--b" role="img" aria-label="Decorative pattern of hanging colour bars"></div>

  <div class="brand"><span class="brand__dot"></span><span class="brand__name">corvane</span></div>
  <p class="brand__tagline">building what comes next</p>

  <div class="contact">
    <p class="contact__email">marcus@corvane.ventures</p>
    <p class="contact__role">Client Ambassador</p>
    <p class="contact__address">Po Box 418 Perth 6000</p>
  </div>

  <p class="phone">
    <svg width="12" height="18" viewBox="0 0 12 18" aria-hidden="true">
      <rect x="1" y="1" width="10" height="16" rx="2" fill="none" stroke="var(--text-soft)" stroke-width="1.5"/>
      <circle cx="6" cy="14" r="1" fill="var(--text-soft)"/>
    </svg>
    <span>+61 040 555 219</span>
  </p>

  <p class="services">Management, software, construction</p>
</section>

<section class="card card--front">
  <div class="pattern pattern--a" role="img" aria-label="Decorative pattern of hanging colour bars"></div>
  <div class="pattern pattern--cool pattern--b" role="img" aria-label="Decorative pattern of hanging colour bars"></div>
  <div class="pattern pattern--warm pattern--c" role="img" aria-label="Decorative pattern of colour bars at the edge"></div>

  <div class="brand"><span class="brand__dot"></span><span class="brand__name">corvane</span></div>
  <p class="brand__tagline">building what comes next</p>
</section>

</body>
</html>
```